post card 4x6

this is a post card that will be sent to plumbing companies and foundation repair companies for whole sale work. if you can add ( work done in unmarked truck -will ware your shirt)

```html
<!DOCTYPE html>
<html lang="en">
<head>
<meta charset="utf-8">
<title>DrainView Wholesale Postcard</title>
<link rel="stylesheet" href="https://fonts.googleapis.com/css2?family=Montserrat:ital,wght@0,400;0,500;0,700;0,800;0,900;1,800;1,900&display=swap">
<style>
  :root {
    --navy: #1f2a3f;
    --navy-deep: #18223a;
    --red: #e94a43;
    --red-strong: #e53b35;
    --white: #ffffff;
    --paper: #f6f7f9;
    --stage: #ececec;
    --coin: #f2b81b;
    --stamp: #e6e7ea;
  }
  * { box-sizing: border-box; margin: 0; padding: 0; }
  html, body { width: 782px; height: 1200px; overflow: hidden; background: var(--stage); }
  body { font-family: "Montserrat", Arial, sans-serif; }
  .canvas { position: relative; width: 782px; height: 1200px; }

  .card { position: absolute; left: 41px; width: 700px; height: 467px; overflow: hidden; }
  .card-front { top: 118px; background: var(--white); }
  .card-back { top: 615px; background: var(--paper); }

  /* Front */
  .front-panel { position: absolute; left: 0; top: 0; width: 393px; height: 467px; background: var(--navy); }
  .brand-name { font-weight: 900; color: var(--red-strong); letter-spacing: 0.5px; white-space: nowrap; }
  .front-brand { position: absolute; top: 28px; left: 0; width: 393px; text-align: center; font-size: 40px; line-height: 1; }
  .headline { position: absolute; left: 40px; top: 103px; color: var(--white); font-weight: 800; text-transform: uppercase; }
  .headline .line { display: block; font-size: 34px; line-height: 33px; letter-spacing: -0.3px; }
  .headline .line-accent { font-size: 55px; line-height: 46px; font-weight: 900; color: var(--red); letter-spacing: -1px; margin-top: 1px; }
  .coin { display: inline-block; width: 27px; height: 27px; border-radius: 50%; background: var(--coin); color: var(--white); font-size: 20px; line-height: 27px; text-align: center; vertical-align: 2px; font-weight: 900; }

  .service-band { position: absolute; left: 0; top: 238px; width: 393px; height: 128px; background: var(--red); }
  .service-list { list-style: none; position: absolute; top: 0; left: 0; width: 100%; height: 100%; }
  .service { position: absolute; color: var(--white); font-weight: 800; font-size: 14.5px; line-height: 14px; text-transform: uppercase; display: flex; align-items: center; white-space: nowrap; }
  .service::before { content: ""; position: absolute; left: -18px; width: 4px; height: 4px; border-radius: 50%; background: var(--white); }
  .service small { font-size: 7px; font-weight: 500; margin-left: 4px; }
  .col-a { left: 44px; }
  .col-b { left: 219px; }
  .row-1 { top: 21px; }
  .row-2 { top: 54px; }
  .row-3 { top: 80px; height: 28px; }
  .service.row-3.col-a { top: 87px; height: 14px; }

  .front-contact { position: absolute; left: 0; top: 366px; width: 393px; height: 101px; }
  .license { position: absolute; right: 20px; top: 6px; color: var(--white); font-size: 10px; font-weight: 500; }
  .contact-row { position: absolute; display: flex; align-items: center; color: var(--white); white-space: nowrap; }
  .icon-dot { display: inline-block; flex: none; border-radius: 50%; background: var(--red); position: relative; }
  .icon-dot svg { position: absolute; left: 0; top: 0; width: 100%; height: 100%; }
  .front-phone { left: 46px; top: 20px; font-size: 34px; font-weight: 900; letter-spacing: -0.3px; }
  .front-phone .icon-dot { width: 16px; height: 16px; margin-right: 18px; }
  .front-web { left: 46px; top: 62px; font-size: 21px; font-weight: 400; letter-spacing: 0.3px; }
  .front-web .icon-dot { width: 16px; height: 16px; margin-right: 18px; }

  .photo { position: absolute; }
  .photo-rusted-pipe { left: 403px; top: 14px; width: 289px; height: 216px; background: radial-gradient(circle at 48% 35%, #1c1208 0 12%, #5a3a18 22%, #a8651f 45%, #b9782e 70%, #8a5a22 100%); }
  .photo-lined-pipe { left: 403px; top: 237px; width: 289px; height: 216px; background: radial-gradient(circle at 33% 37%, #1d2c22 0 6%, #1f6b48 14%, #2b8a5d 45%, #217a4f 100%); }

  /* Back */
  .back-banner { position: absolute; left: 0; top: 0; width: 351px; height: 151px; background: linear-gradient(90deg, var(--navy-deep) 0%, #243352 100%); }
  .back-headline { position: absolute; left: 27px; top: 32px; font-weight: 900; text-transform: uppercase; color: var(--white); white-space: nowrap; }
  .back-headline .l1 { display: block; font-size: 30px; line-height: 30px; letter-spacing: 0.3px; }
  .back-headline .l2 { display: block; font-size: 24px; line-height: 25px; letter-spacing: 0.2px; }
  .back-headline .l3 { display: block; font-size: 21px; line-height: 23px; color: var(--red); letter-spacing: 0.2px; }
  .illustration-plumber { position: absolute; left: 328px; top: 8px; width: 74px; height: 143px; background: linear-gradient(180deg, #3d7fc4 0%, #2f6fb3 60%, #c8393a 100%); border-radius: 8px; opacity: 0.9; }

  .photo-grid .photo { width: 167px; height: 111px; }
  .photo-trench { left: 9px; top: 158px; background: linear-gradient(160deg, #5b5347, #3c352c 60%, #6b5f4e); }
  .photo-basement { left: 184px; top: 158px; background: linear-gradient(160deg, #7a6e60, #3a3129 55%, #a39a8c); }
  .photo-risers { left: 9px; top: 275px; background: linear-gradient(170deg, #5d4535, #3b2b22 60%, #c9c2b6); }
  .photo-camera { left: 184px; top: 275px; background: linear-gradient(160deg, #b7b4ad, #8f8c86 55%, #5c5a56); }

  .back-footer { position: absolute; left: 0; top: 403px; width: 351px; height: 64px; background: var(--red); }
  .ribbon { position: absolute; left: 23px; top: 393px; height: 36px; width: 307px; }
  .ribbon svg { position: absolute; inset: 0; width: 100%; height: 100%; }
  .ribbon-call { position: absolute; left: 26px; top: 0; line-height: 36px; color: var(--white); font-weight: 800; font-size: 13px; white-space: nowrap; }
  .ribbon-offer { position: absolute; left: 127px; top: 0; line-height: 36px; color: var(--white); font-weight: 900; font-style: italic; font-size: 12.5px; white-space: nowrap; }
  .back-phone { left: 15px; top: 440px; font-size: 20px; font-weight: 900; }
  .back-phone .icon-dot, .back-web .icon-dot { width: 10px; height: 10px; margin-right: 7px; background: var(--navy); }
  .back-web { left: 192px; top: 445px; font-size: 11px; font-weight: 500; }

  .back-brand { position: absolute; left: 409px; top: 30px; font-size: 27px; line-height: 1; }
  .stamp-box { position: absolute; left: 619px; top: 25px; width: 62px; height: 62px; background: var(--stamp); }
</style>
</head>
<body>
<div class="canvas">

  <section class="card card-front" aria-label="Postcard front">
    <div class="front-panel">
      <div class="brand-name front-brand">DrainView</div>
      <h1 class="headline">
        <span class="line">You make the</span>
        <span class="line">D<span class="coin">$</span>llar we do</span>
        <span class="line line-accent">The work</span>
      </h1>

      <div class="service-band">
        <ul class="service-list">
          <li class="service col-a row-1">CIPP<small>(Cured in place pipe)</small></li>
          <li class="service col-a row-2">SIPP<small>(Spray in place pipe)</small></li>
          <li class="service col-a row-3">Pipe bursting</li>
          <li class="service col-b row-1">Hydro jetting</li>
          <li class="service col-b row-2">Resize cast iron</li>
          <li class="service col-b row-3">Sewer camera<br>and locate</li>
        </ul>
      </div>

      <div class="front-contact">
        <div class="license">RMP#51207</div>
        <div class="contact-row front-phone">
          <span class="icon-dot"><svg viewBox="0 0 16 16"><path d="M5.6 4.2 6.8 6c.2.3.1.6-.1.8l-.7.6c.5 1 1.3 1.8 2.3 2.4l.6-.7c.2-.2.5-.3.8-.1l1.8 1.2c.3.2.3.5.1.8l-.8.9c-.4.4-1 .5-1.5.3-2.3-1-4-2.8-4.9-5.1-.2-.5-.1-1.1.3-1.5l.9-.7c.2-.2.6-.1.8.1z" fill="#fff"/></svg></span>
          555-014-2290
        </div>
        <div class="contact-row front-web">
          <span class="icon-dot"><svg viewBox="0 0 16 16"><circle cx="8" cy="8" r="4.2" fill="none" stroke="#fff" stroke-width="1.1"/><ellipse cx="8" cy="8" rx="1.8" ry="4.2" fill="none" stroke="#fff" stroke-width="1"/><path d="M3.8 8h8.4" stroke="#fff" stroke-width="1"/></svg></span>
          WWW.DRAINVIEW.COM
        </div>
      </div>
    </div>

    <div class="photo photo-rusted-pipe" role="img" aria-label="Camera view inside a corroded cast iron sewer pipe"></div>
    <div class="photo photo-lined-pipe" role="img" aria-label="Camera view inside a smooth green relined pipe"></div>
  </section>

  <section class="card card-back" aria-label="Postcard back">
    <div class="back-banner">
      <h2 class="back-headline">
        <span class="l1">Workdone in</span>
        <span class="l2">Unmarked truck -</span>
        <span class="l3">Will ware your shirt</span>
      </h2>
    </div>
    <div class="illustration-plumber" role="img" aria-label="Illustrated plumber in overalls holding a wrench and toolbox"></div>

    <div class="photo-grid">
      <div class="photo photo-trench" role="img" aria-label="Excavated trench with exposed sewer line"></div>
      <div class="photo photo-basement" role="img" aria-label="New black drain pipes installed in a basement floor"></div>
      <div class="photo photo-risers" role="img" aria-label="Replaced pipe risers in an open trench"></div>
      <div class="photo photo-camera" role="img" aria-label="Sewer inspection camera monitor beside a floor drain"></div>
    </div>

    <div class="back-footer"></div>
    <div class="ribbon">
      <svg viewBox="0 0 307 36" preserveAspectRatio="none">
        <polygon points="14,0 100,0 108,18 100,36 0,36" fill="#e94a43" stroke="#fff" stroke-width="2"/>
        <polygon points="100,0 307,0 293,36 100,36 108,18" fill="#1f2a3f" stroke="#fff" stroke-width="2"/>
      </svg>
      <span class="ribbon-call">CALL FOR</span>
      <span class="ribbon-offer">WHOLE SALE PRICING</span>
    </div>
    <div class="contact-row back-phone">
      <span class="icon-dot"><svg viewBox="0 0 16 16"><path d="M5.6 4.2 6.8 6c.2.3.1.6-.1.8l-.7.6c.5 1 1.3 1.8 2.3 2.4l.6-.7c.2-.2.5-.3.8-.1l1.8 1.2c.3.2.3.5.1.8l-.8.9c-.4.4-1 .5-1.5.3-2.3-1-4-2.8-4.9-5.1-.2-.5-.1-1.1.3-1.5l.9-.7c.2-.2.6-.1.8.1z" fill="#fff"/></svg></span>
      555-014-2290
    </div>
    <div class="contact-row back-web">
      <span class="icon-dot"><svg viewBox="0 0 16 16"><circle cx="8" cy="8" r="4.2" fill="none" stroke="#fff" stroke-width="1.3"/><path d="M3.8 8h8.4M8 3.8v8.4" stroke="#fff" stroke-width="1.1"/></svg></span>
      WWW.DRAINVIEW.COM
    </div>

    <div class="brand-name back-brand">DrainView</div>
    <div class="stamp-box" aria-label="Postage stamp area"></div>
  </section>

</div>
</body>
</html>
```